Lakeshore Grain Corporate Powerpoint Template

We need a standardized corporate PowerPoint template that can be used for employees to create presentations with for events, meetings, and trainings. Our logo is blue, red, and white. I would like to feature the logo on each page and I visualize the "title page" to be navy blue based and "scream" Lakeshore Grain Company. I do not want the slide pages they use for content to be too busy, but still visually pleasing.

```html
<!DOCTYPE html>
<html lang="en">
<head>
<meta charset="utf-8">
<title>Lakeshore Grain – Corporate Presentation Template</title>
<link href="https://fonts.googleapis.com/css2?family=Michroma&family=Merriweather+Sans:wght@300;400;700&family=Oswald:wght@400;500&display=swap" rel="stylesheet">
<style>
:root{
  --stage:#9a9a9a;
  --navy:#2b3a96;
  --royal:#1d5bb0;
  --red:#e0343b;
  --ink:#3a3a3a;
  --body:#555;
  --white:#fff;
  --mauve:#8b5a7a;
  --pie-main:#2a3fb5;
  --pie-lilac:#aeb0e8;
  --pie-rose:#e06f98;
  --pie-blush:#f3b6c4;
}
*{box-sizing:border-box;margin:0;padding:0}
html,body{width:1071px;height:1200px;overflow:hidden;background:var(--stage)}
body{position:relative;font-family:"Merriweather Sans",sans-serif;color:var(--ink)}
.slide{position:absolute;width:426px;height:240px;background:var(--white);overflow:hidden;box-shadow:2px 3px 5px rgba(0,0,0,.35)}
.col-a{left:99.5px}.col-b{left:545.5px}
.row-1{top:97px}.row-2{top:352.5px}.row-3{top:608px}.row-4{top:863px}
.abs{position:absolute}
.slide-title{position:absolute;left:23px;top:15px;font-family:"Michroma",sans-serif;font-size:15px;letter-spacing:1.5px;color:var(--red);font-weight:400;-webkit-text-stroke:.6px var(--red)}
.brand{position:absolute;right:18px;top:12px;display:flex;align-items:center;gap:3px;font-family:"Merriweather Sans",sans-serif;font-weight:700;font-size:6.5px;color:var(--navy);letter-spacing:.3px}
.brand .mark{width:7px;height:7px;background:var(--navy)}
.footer{position:absolute;left:0;bottom:0;width:100%;height:18px;background:var(--navy);color:var(--white);font-size:6.4px;font-weight:300;display:flex;align-items:center}
.footer .line{flex:1;display:flex;justify-content:center;align-items:center;gap:3px;white-space:nowrap;padding-left:8px}
.footer svg{width:7px;height:7px;fill:var(--white)}
.footer .page{width:20px;height:18px;background:var(--red);display:flex;align-items:center;justify-content:center;font-size:5.5px}
.frame{position:absolute;border:1.5px solid var(--red)}
.photo{position:absolute}
.play{position:absolute;width:17px;height:17px;border-radius:50%;background:var(--red);display:flex;align-items:center;justify-content:center}
.text{position:absolute;font-size:6.3px;line-height:10px;color:var(--body);text-align:justify;font-weight:300}
.text p+p{margin-top:8px}
.dot-page{position:absolute;width:12px;height:12px;border-radius:50%;background:var(--red);color:var(--white);font-size:5px;display:flex;align-items:center;justify-content:center;right:6px;bottom:7px}
.cover-field{background:linear-gradient(180deg,#3e77c6 0%,#2460b6 30%,#1a4ea3 60%,#143f8c 100%)}
.cover-brand{position:absolute;left:50%;transform:translateX(-50%);display:flex;align-items:center;gap:5px;font-weight:700;color:var(--white);letter-spacing:.8px;white-space:nowrap}
.cover-brand .mark{background:var(--red)}
.cover-title{position:absolute;left:0;width:100%;text-align:center;font-family:"Michroma",sans-serif;color:var(--white);-webkit-text-stroke:.5px var(--white)}
.date-tag{position:absolute;left:158px;top:160px;width:111px;height:20px;background:var(--red);color:var(--white);font-weight:700;font-size:8px;letter-spacing:.5px;display:flex;align-items:center;justify-content:center}
.soft-bg{background:linear-gradient(135deg,#f7f7f7 0%,#eeeeee 40%,#f8f8f8 70%,#ffffff 100%)}
.option{position:absolute;width:58px}
.option .pill{height:21px;border:1.2px solid currentColor;border-radius:11px;display:flex;align-items:center;background:var(--white)}
.option .num{font-family:"Oswald",sans-serif;font-size:7.5px;width:20px;text-align:center}
.option .tag{flex:1;height:15px;margin-right:2px;border-radius:8px;color:var(--white);font-family:"Oswald",sans-serif;font-size:6.3px;display:flex;align-items:center;padding-left:4px}
.option .card{height:46px;border:1px solid currentColor;border-top:none;border-radius:0 0 9px 9px;margin-top:-1px;text-align:center;padding-top:5px;background:var(--white)}
.option .icon{width:11px;height:11px;border:1px solid currentColor;border-radius:50%;margin:0 auto 3px}
.option .card p{font-size:3px;line-height:4px;padding:0 7px}
.opt-blue{color:var(--royal)}.opt-blue .tag{background:var(--royal)}
.opt-mauve{color:var(--mauve)}.opt-mauve .tag{background:var(--mauve)}
.opt-red{color:var(--red)}.opt-red .tag{background:var(--red)}
.reason{position:absolute;left:233px;width:176px}
.reason .check{position:absolute;left:0;top:-2px;width:13px;height:13px;display:flex;align-items:center;justify-content:center}
.reason h3{margin-left:22px;font-size:7.6px;font-weight:700;color:#333}
.reason p{margin-left:22px;margin-top:6px;font-size:5.2px;line-height:9.5px;color:var(--body);font-weight:300}
.caption{position:absolute;width:116px;text-align:center;font-size:5.8px;line-height:8px;font-weight:700;color:#222}
.pie-label{font-family:"Oswald",sans-serif;fill:var(--white);text-anchor:middle}
.meet-head{position:absolute;left:221px;top:57px;font-size:9.3px;font-weight:400;color:#222}
.thanks-field{background:radial-gradient(ellipse at 50% 110%,#2a68bf 0%,#1c57aa 45%,#14478f 100%)}
.contact{position:absolute;top:166px;display:flex;align-items:center;gap:7px;color:var(--white);font-weight:700;font-size:8px;white-space:nowrap}
.contact .box{width:18px;height:18px;display:flex;align-items:center;justify-content:center}
</style>
</head>
<body>

<section class="slide col-a row-1 cover-field" role="img" aria-label="Cover background: wide field of green crop rows under a sky, tinted deep blue">
  <div class="cover-brand" style="top:72px;font-size:11px"><span class="mark" style="width:9px;height:9px"></span>LAKESHORE GRAIN</div>
  <h1 class="cover-title" style="top:132px;font-size:14.5px;letter-spacing:1.6px">PRESENTATIION TITLE HERE</h1>
  <div class="date-tag">OCTOBER 25,2024</div>
  <div class="dot-page">01</div>
</section>

<section class="slide col-b row-1">
  <h2 class="slide-title">TRAININGS</h2>
  <div class="brand"><span class="mark"></span>LAKESHORE GRAIN</div>
  <div class="frame" style="left:22px;top:55px;width:97px;height:117px"></div>
  <div class="photo" role="img" aria-label="Video still: speaker at a podium addressing a training session in front of a company banner" style="left:33px;top:65px;width:169px;height:126px;background:linear-gradient(135deg,#3a3a3e,#8c8a86 55%,#3f4f8a)"></div>
  <div class="play" style="left:109px;top:119px"><svg width="7" height="7" viewBox="0 0 10 10"><path d="M2 1 9 5 2 9Z" fill="#fff"/></svg></div>
  <div class="frame" style="left:302px;top:55px;width:97px;height:117px"></div>
  <div class="photo" role="img" aria-label="Video still: presenter in a blue shirt speaking at a lectern on a stage" style="left:219.5px;top:65px;width:169px;height:126px;background:linear-gradient(135deg,#2c2c30,#556a9e 50%,#6b5a5a)"></div>
  <div class="play" style="left:295.5px;top:119px"><svg width="7" height="7" viewBox="0 0 10 10"><path d="M2 1 9 5 2 9Z" fill="#fff"/></svg></div>
  <footer class="footer"><div class="line"><svg viewBox="0 0 10 10"><path d="M0 2 3 1 7 2 10 1V8L7 9 3 8 0 9Z"/></svg>48 Harbor Lane &nbsp;|&nbsp; Suite 210 &nbsp;|&nbsp; Port Aldin, Ohio 44011 &nbsp;| <svg viewBox="0 0 10 10"><path d="M2 0 4 2 3 4Q5 6 6 7L8 6 10 8 8 10Q0 8 0 2Z"/></svg> PHONE: 555-201-0147 &nbsp;| <svg viewBox="0 0 10 10"><path d="M1 3H9V10H1ZM3 0H7V3H3Z"/></svg> FAX: 555-201-0183</div><div class="page">05</div></footer>
</section>

<section class="slide col-a row-2">
  <h2 class="slide-title">ABOUT US</h2>
  <div class="brand"><span class="mark"></span>LAKESHORE GRAIN</div>
  <div class="text" style="left:23.5px;top:47px;width:186px">
    <p>After loggers had cleared the pine forests in the area, the land was virtually unusable due to the massive expanse of tree stumps left behind. State and local leaders were searching for a substitute for the jobs and money generated by now-departed lumber barons. A solution was needed that could be replenished each year, bringing a stabilizing influence on the economic base of the region.</p>
    <p>In 1839, Thomas Avery, a skilled potato grower, decided he could transfer his talents to the planting of the sugarbeet. His growing project was successful, but the manufacturing system was not.Interest in the sugarbeet was not revived until 1884, when Henry Lindqvist, a Westfield printer, happened to see how well the sugarbeet was doing for the people in a region of Germany that he visited.</p>
  </div>
  <div class="frame" style="left:270.7px;top:71px;width:88px;height:106px"></div>
  <div class="photo" role="img" aria-label="Archival sepia portrait of a company founder in a suit" style="left:329.5px;top:48px;width:89px;height:107px;background:linear-gradient(160deg,#8a7a66,#4a3f34 60%,#2e2620)"></div>
  <div class="photo" role="img" aria-label="Historic photo of two executives signing documents at a desk" style="left:236.5px;top:97.7px;width:89px;height:106.5px;background:linear-gradient(160deg,#b9b3a2,#6d6257 55%,#5b3d2a)"></div>
  <footer class="footer"><div class="line"><svg viewBox="0 0 10 10"><path d="M0 2 3 1 7 2 10 1V8L7 9 3 8 0 9Z"/></svg>48 Harbor Lane &nbsp;|&nbsp; Suite 210 &nbsp;|&nbsp; Port Aldin, Ohio 44011 &nbsp;| <svg viewBox="0 0 10 10"><path d="M2 0 4 2 3 4Q5 6 6 7L8 6 10 8 8 10Q0 8 0 2Z"/></svg> PHONE: 555-201-0147 &nbsp;| <svg viewBox="0 0 10 10"><path d="M1 3H9V10H1ZM3 0H7V3H3Z"/></svg> FAX: 555-201-0183</div><div class="page">02</div></footer>
</section>

<section class="slide col-b row-2 soft-bg">
  <h2 class="slide-title">WHY CHOOSE US</h2>
  <div class="brand"><span class="mark"></span>LAKESHORE GRAIN</div>
  <div class="option opt-blue" style="left:16.5px;top:93px"><div class="pill"><span class="num">01</span><span class="tag">OPTION</span></div><div class="card"><div class="icon"></div><p>Lorem ipsum dolor sit amet, consectetur adipiscing elit sed do eiusmod tempor</p></div></div>
  <div class="option opt-mauve" style="left:84px;top:73px"><div class="pill"><span class="num">02</span><span class="tag">OPTION</span></div><div class="card"><div class="icon"></div><p>Lorem ipsum dolor sit amet, consectetur adipiscing elit sed do eiusmod tempor</p></div></div>
  <div class="option opt-red" style="left:151px;top:93px"><div class="pill"><span class="num">03</span><span class="tag">OPTION</span></div><div class="card"><div class="icon"></div><p>Lorem ipsum dolor sit amet, consectetur adipiscing elit sed do eiusmod tempor</p></div></div>
  <div class="reason" style="top:48px"><span class="check" style="background:var(--royal)"><svg width="9" height="9" viewBox="0 0 10 10"><path d="M1.5 5 4 7.5 8.5 2.5" stroke="#fff" stroke-width="1.6" fill="none"/></svg></span><h3>Duis aute irure dolorrehenderit</h3><p>Sed ut perspiciatis unde omnis iste natus error sit voluptatem accusantium doloremque laudantium, totam rem aperiam, eaque ipsa quae ab illo inventore veritatis et quasi</p></div>
  <div class="reason" style="top:106px"><span class="check" style="background:var(--mauve)"><svg width="9" height="9" viewBox="0 0 10 10"><path d="M1.5 5 4 7.5 8.5 2.5" stroke="#fff" stroke-width="1.6" fill="none"/></svg></span><h3>Duis aute irure dolorrehenderit</h3><p>Sed ut perspiciatis unde omnis iste natus error sit voluptatem accusantium doloremque laudantium, totam rem aperiam, eaque ipsa quae ab illo inventore veritatis et quasi</p></div>
  <div class="reason" style="top:164px"><span class="check" style="background:var(--red)"><svg width="9" height="9" viewBox="0 0 10 10"><path d="M1.5 5 4 7.5 8.5 2.5" stroke="#fff" stroke-width="1.6" fill="none"/></svg></span><h3>Duis aute irure dolorrehenderit</h3><p>Sed ut perspiciatis unde omnis iste natus error sit voluptatem accusantium doloremque laudantium, totam rem aperiam, eaque ipsa quae ab illo inventore veritatis et quasi</p></div>
  <footer class="footer"><div class="line"><svg viewBox="0 0 10 10"><path d="M0 2 3 1 7 2 10 1V8L7 9 3 8 0 9Z"/></svg>48 Harbor Lane &nbsp;|&nbsp; Suite 210 &nbsp;|&nbsp; Port Aldin, Ohio 44011 &nbsp;| <svg viewBox="0 0 10 10"><path d="M2 0 4 2 3 4Q5 6 6 7L8 6 10 8 8 10Q0 8 0 2Z"/></svg> PHONE: 555-201-0147 &nbsp;| <svg viewBox="0 0 10 10"><path d="M1 3H9V10H1ZM3 0H7V3H3Z"/></svg> FAX: 555-201-0183</div><div class="page">06</div></footer>
</section>

<section class="slide col-a row-3">
  <h2 class="slide-title">EVENTS</h2>
  <div class="brand"><span class="mark"></span>LAKESHORE GRAIN</div>
  <div class="frame" style="left:22.4px;top:54px;width:97.7px;height:116.5px"></div>
  <div class="photo" role="img" aria-label="Event photo: newly crowned festival queen with sashes and bouquets" style="left:33.5px;top:64.7px;width:97px;height:116.5px;background:linear-gradient(160deg,#6f9fd0,#c9a7a4 45%,#2c3e78 80%)"></div>
  <div class="frame" style="left:159px;top:54px;width:97.7px;height:116.5px"></div>
  <div class="photo" role="img" aria-label="Event photo: speaker at a lectern in front of a company banner" style="left:169.5px;top:64.7px;width:97px;height:116.5px;background:linear-gradient(160deg,#3d56a6,#2f2f33 55%,#7d6b6b)"></div>
  <div class="frame" style="left:295.4px;top:54px;width:97.7px;height:116.5px"></div>
  <div class="photo" role="img" aria-label="Event photo: stainless steel tanks inside a new processing facility" style="left:306px;top:64.7px;width:97px;height:116.5px;background:linear-gradient(160deg,#c9c9c7,#7d7e7c 50%,#4a4b4a)"></div>
  <p class="caption" style="left:24px;top:187px">Lakeshore Grain Company cuts the ribbon on new Molasses Desugarization Facility in Port Aldin</p>
  <p class="caption" style="left:160px;top:187px">Clara Hensley of Millbrook crowned 2024 Lakeshore Grain Queen</p>
  <p class="caption" style="left:296px;top:187px">Lakeshore Grain Company Starts Up Molasses Desugarization Facility</p>
  <footer class="footer"><div class="line"><svg viewBox="0 0 10 10"><path d="M0 2 3 1 7 2 10 1V8L7 9 3 8 0 9Z"/></svg>48 Harbor Lane &nbsp;|&nbsp; Suite 210 &nbsp;|&nbsp; Port Aldin, Ohio 44011 &nbsp;| <svg viewBox="0 0 10 10"><path d="M2 0 4 2 3 4Q5 6 6 7L8 6 10 8 8 10Q0 8 0 2Z"/></svg> PHONE: 555-201-0147 &nbsp;| <svg viewBox="0 0 10 10"><path d="M1 3H9V10H1ZM3 0H7V3H3Z"/></svg> FAX: 555-201-0183</div><div class="page">03</div></footer>
</section>

<section class="slide col-b row-3">
  <div class="abs soft-bg" style="left:0;top:0;width:184px;height:222px"></div>
  <h2 class="slide-title">OUR GRAPH</h2>
  <svg class="abs" style="left:0;top:0" width="426" height="222" viewBox="0 0 426 222" role="img" aria-label="Pie chart: 60%, 15%, 10% and 5% shares">
    <path d="M294 112 L294 12 A100 100 0 1 1 223.3 182.7Z" fill="var(--pie-main)"/>
    <path d="M294 112 L241 165 A75 75 0 0 1 219 112Z" fill="var(--pie-blush)"/>
    <path d="M294 112 L210 112 A84 84 0 0 1 234.6 52.6Z" fill="var(--pie-rose)"/>
    <path d="M294 112 L229.7 47.7 A91 91 0 0 1 294 21Z" fill="var(--pie-lilac)"/>
    <text class="pie-label" x="267" y="48" font-size="5.5">LOREM IPSUM</text>
    <text class="pie-label" x="267" y="60" font-size="5.5">15%</text>
    <text class="pie-label" x="246" y="93" font-size="5.5">LOREM IPSUM</text>
    <text class="pie-label" x="246" y="105" font-size="5.5">10%</text>
    <text class="pie-label" x="248" y="128" font-size="5.5">LOREM IPSUM</text>
    <text class="pie-label" x="248" y="140" font-size="5.5">5%</text>
    <text class="pie-label" x="311" y="175" font-size="9">LOREM IPSUM</text>
    <text class="pie-label" x="311" y="192" font-size="9">60%</text>
  </svg>
  <div class="brand"><span class="mark"></span>LAKESHORE GRAIN</div>
  <div class="text" style="left:22.4px;top:60px;width:158px;font-size:5.3px;line-height:9.5px">
    <p>Sed ut perspiciatis unde omnis iste natus error sit voluptatem accusantium doloremque laudantium, totam rem aperiaSed ut perspiciatis unde omnis iste natus error sit voluptatem accusantium doloremque laudantium, totam rem aperiam, eaque ipsa quae ab illo inventore veritatis et quasi ipisci velit, sed quia non numquam eius modi tempora incidunt ut laboremagnam aliqua.Sed ut perspiciatis unde omnis iste natus error sit voluptatem accusantium doloremque laudantium, totam rem aperiam, eaque ipsa quae ab illo inventore veriquasi</p>
    <p>Adipisci velit, sed quia non numquam eius modi tempora incidunt ut laboremagnam aliqua.Sed ut perspiciatis unde omnis iste natus error sit voluptatem accusantium doloremque laudantium, totam rem aperiam, eaque ipsa quae ab illo inventore veritatis et quasi</p>
  </div>
  <footer class="footer"><div class="line"><svg viewBox="0 0 10 10"><path d="M0 2 3 1 7 2 10 1V8L7 9 3 8 0 9Z"/></svg>48 Harbor Lane &nbsp;|&nbsp; Suite 210 &nbsp;|&nbsp; Port Aldin, Ohio 44011 &nbsp;| <svg viewBox="0 0 10 10"><path d="M2 0 4 2 3 4Q5 6 6 7L8 6 10 8 8 10Q0 8 0 2Z"/></svg> PHONE: 555-201-0147 &nbsp;| <svg viewBox="0 0 10 10"><path d="M1 3H9V10H1ZM3 0H7V3H3Z"/></svg> FAX: 555-201-0183</div><div class="page">07</div></footer>
</section>

<section class="slide col-a row-4">
  <h2 class="slide-title">MEETINGS</h2>
  <div class="brand"><span class="mark"></span>LAKESHORE GRAIN</div>
  <div class="frame" style="left:22.4px;top:54px;width:97.7px;height:115.5px"></div>
  <div class="photo" role="img" aria-label="Meeting photo: large audience seated in a white tent listening to a speaker" style="left:33.5px;top:64.7px;width:168px;height:139px;background:linear-gradient(170deg,#d9d9d6 0%,#b7b4ad 35%,#6f6a78 60%,#3c4a7a 100%)"></div>
  <h3 class="meet-head">Duis aute irure dolor in reprehenderit</h3>
  <div class="text" style="left:221px;top:77px;width:186px;line-height:11.2px">
    <p>Sed ut perspiciatis unde omnis iste natus error sit voluptatem accusantium doloremque laudantium, totam rem aperiam, eaque ipsa quae ab illo inventore veritatis et quasi architecto beatae vitae dicta sunt explicabo. Nemo enim ipsam voluptatem quia voluptas sit aspernatur aut odit aut fugit, sed quia consequuntur magni dolores eos qui ratione voluptatem sequi nesciunt.</p>
    <p>Neque porro quisquam est, qui dolorem ipsum quia dolor sit amet, consectetur, adipisci velit, sed quia non numquam eius modi tempora incidunt ut laboremagnam aliquam quaerati dolorem ipsum quia dolor sit amet, consectetu</p>
  </div>
  <footer class="footer"><div class="line"><svg viewBox="0 0 10 10"><path d="M0 2 3 1 7 2 10 1V8L7 9 3 8 0 9Z"/></svg>48 Harbor Lane &nbsp;|&nbsp; Suite 210 &nbsp;|&nbsp; Port Aldin, Ohio 44011 &nbsp;| <svg viewBox="0 0 10 10"><path d="M2 0 4 2 3 4Q5 6 6 7L8 6 10 8 8 10Q0 8 0 2Z"/></svg> PHONE: 555-201-0147 &nbsp;| <svg viewBox="0 0 10 10"><path d="M1 3H9V10H1ZM3 0H7V3H3Z"/></svg> FAX: 555-201-0183</div><div class="page">04</div></footer>
</section>

<section class="slide col-b row-4 thanks-field" role="img" aria-label="Closing background: large pile of harvested crop, tinted blue">
  <div class="cover-brand" style="top:72px;font-size:11px"><span class="mark" style="width:9px;height:9px"></span>LAKESHORE GRAIN</div>
  <h2 class="cover-title" style="top:128px;font-size:20px;letter-spacing:2px">THANK YOU</h2>
  <div class="contact" style="left:73px"><span class="box" style="background:var(--red)"><svg width="9" height="9" viewBox="0 0 10 10"><path d="M2 0 4 2 3 4Q5 6 6 7L8 6 10 8 8 10Q0 8 0 2Z" fill="#fff"/></svg></span>CALL US : +1 888 888 8888</div>
  <div class="contact" style="left:223px"><span class="box" style="border:1px solid #fff"><svg width="9" height="7" viewBox="0 0 10 8"><path d="M0 0H10V8H0Z" fill="#fff"/><path d="M0 0 5 4 10 0" stroke="#1c57aa" fill="none"/></svg></span><span style="margin-left:3px">info@companyname.com</span></div>
  <div class="dot-page">08</div>
</section>

</body>
</html>
```